landscaping core flute signs

I need core flutes created with business name and a few extra dot points for putting on fences for job sites 120cm x 120cm approx.
I want our old ones information with the new L logo and colour palette

```html
<!DOCTYPE html>
<html lang="en">
<head>
<meta charset="utf-8">
<title>Stonefield Grounds – Site Sign</title>
<link rel="stylesheet" href="https://fonts.googleapis.com/css2?family=Poppins:wght@600;700;800&display=swap">
<style>
  :root {
    --backdrop: #555555;
    --ink: #000000;
    --paper: #ffffff;
    --leaf: #568a4b;
  }
  * { box-sizing: border-box; margin: 0; padding: 0; }
  html, body {
    width: 671px; height: 1200px; overflow: hidden;
    background: var(--backdrop);
    font-family: "Poppins", sans-serif;
  }
  .sign {
    position: absolute; left: 36px; top: 300px;
    width: 600px; height: 600px;
    background: var(--paper);
    overflow: hidden;
    box-shadow: 0 4px 14px rgba(0,0,0,0.35);
  }
  .sign__top {
    position: absolute; left: 0; top: 0; width: 600px; height: 372px;
    background: var(--ink);
  }
  .brand {
    position: absolute; left: 57px; top: 36px; height: 123px;
    display: flex; align-items: center; gap: 20px;
  }
  .brand__dot {
    width: 122px; height: 122px; border-radius: 50%;
    background: var(--leaf); flex: none;
  }
  .brand__name {
    color: var(--paper); font-weight: 700;
    font-size: 44px; line-height: 1.02; letter-spacing: 2px;
  }
  .service {
    position: absolute; left: 40px; width: 522px; height: 59px;
    border: 3px solid var(--leaf); border-radius: 30px;
    background: var(--ink);
    display: flex; align-items: center;
  }
  .service--paving { top: 197px; }
  .service--fencing { top: 269px; }
  .service--design { top: 339px; }
  .service__tick {
    position: absolute; left: 12px; top: 50%; transform: translateY(-50%);
    width: 34px; height: 34px;
  }
  .service__label {
    position: absolute; left: 58px;
    color: var(--paper); font-weight: 800;
    font-size: 29px; letter-spacing: 3.6px; white-space: nowrap;
  }
  .contact-phone {
    position: absolute; left: 27px; top: 436px;
    display: flex; align-items: center; gap: 14px;
  }
  .contact-phone__icon { width: 59px; height: 59px; flex: none; }
  .contact-phone__number {
    font-weight: 800; font-size: 78px; line-height: 1;
    letter-spacing: -2px; color: var(--ink); white-space: nowrap;
  }
  .contact-email {
    position: absolute; left: 27px; top: 520px;
    display: flex; align-items: center; gap: 16px;
  }
  .contact-email__icon { width: 30px; height: 24px; flex: none; }
  .contact-email__address {
    font-weight: 600; font-size: 33px; line-height: 1;
    color: var(--leaf); letter-spacing: -0.4px; white-space: nowrap;
  }
  .licence {
    position: absolute; left: 179px; top: 569px; width: 238px; height: 32px;
  }
  .licence svg { position: absolute; inset: 0; }
  .licence__text {
    position: absolute; inset: 0; display: flex; align-items: center; justify-content: center;
    color: var(--paper); font-weight: 700; font-size: 14px; letter-spacing: 4.5px;
    padding-top: 2px;
  }
</style>
</head>
<body>
  <main class="sign">
    <div class="sign__top"></div>

    <div class="brand">
      <div class="brand__dot"></div>
      <div class="brand__name">STONEFIELD<br>GROUNDS</div>
    </div>

    <div class="service service--paving">
      <svg class="service__tick" viewBox="0 0 34 34" aria-hidden="true">
        <circle cx="17" cy="17" r="17" fill="var(--leaf)"/>
        <path d="M9 17.5l5.5 5.5L25.5 12" fill="none" stroke="#fff" stroke-width="3.6" stroke-linecap="round" stroke-linejoin="round"/>
      </svg>
      <span class="service__label">PAVING &amp; CONCRETING</span>
    </div>

    <div class="service service--fencing">
      <span class="service__label">FENCING &amp; RETAINING</span>
    </div>

    <div class="service service--design">
      <svg class="service__tick" viewBox="0 0 34 34" aria-hidden="true">
        <circle cx="17" cy="17" r="17" fill="var(--leaf)"/>
        <path d="M9 17.5l5.5 5.5L25.5 12" fill="none" stroke="#fff" stroke-width="3.6" stroke-linecap="round" stroke-linejoin="round"/>
      </svg>
      <span class="service__label">DESIGN &amp; CONSTRUCT</span>
    </div>

    <div class="contact-phone">
      <svg class="contact-phone__icon" viewBox="0 0 60 60" aria-hidden="true">
        <circle cx="30" cy="30" r="30" fill="var(--leaf)"/>
        <path d="M22 18c1.5-1.2 3-1 3.8.4l2.6 4.4c.8 1.3.4 2.6-.8 3.4l-1.6 1.1c1.2 3 3.4 5.4 6.2 6.9l1.2-1.5c.9-1.1 2.2-1.4 3.4-.6l4.2 2.8c1.3.9 1.4 2.4.2 3.8l-1.6 1.8c-1.6 1.7-4.2 2-6.6.8-6.4-3.2-11-8.4-13.2-15-.8-2.4-.2-4.8 1.6-6.2z" fill="none" stroke="#000" stroke-width="2.6" stroke-linejoin="round"/>
        <path d="M33 17a10 10 0 0 1 9 9M32.5 22a5 5 0 0 1 4.5 4.5" fill="none" stroke="#000" stroke-width="2.2" stroke-linecap="round"/>
      </svg>
      <span class="contact-phone__number">0412 555 307</span>
    </div>

    <div class="contact-email">
      <svg class="contact-email__icon" viewBox="0 0 30 24" aria-hidden="true">
        <rect x="1.5" y="1.5" width="27" height="21" rx="3" fill="none" stroke="#000" stroke-width="3"/>
        <path d="M3 4l12 9 12-9" fill="none" stroke="#000" stroke-width="3" stroke-linejoin="round"/>
      </svg>
      <span class="contact-email__address">sam@stonefieldgrounds.com</span>
    </div>

    <div class="licence">
      <svg viewBox="0 0 238 32" preserveAspectRatio="none" aria-hidden="true">
        <path d="M0 32 C10 32 12 26 16 16 C20 5 26 0 40 0 H198 C212 0 218 5 222 16 C226 26 228 32 238 32 Z" fill="var(--leaf)"/>
      </svg>
      <span class="licence__text">QBSA: 2047316</span>
    </div>
  </main>
</body>
</html>
```